We Buy Houses Postcard Design

Harborline Asset Partners is one of Baltimore‘s top real estate investing groups because we treat buyers and sellers like real people; not like numbers on a spreadsheet. We specialize in buying distressed properties including multi-family, commercial, retail, single family, and bank REO’s from sellers who need to sell fast. Our website is www.harborlineassetpartners.com. Our phone number is (555) 274-1916. Both need to be on the card. Front and back sides are to be printed. Front full color, back black and white. We want our logo on the design somewhere. The logo can be found on the website. If you need the original files ask me for them. See attached as examples. Return address should be 587 W Tessaly Ave, Suite 319, Baltimore, MD 21209. My name is Marcus. Address label is 1" x 2-5/8". Please leave room for it and postage on the back side.

Industry/Entity Type

Real Estate

```html
<!DOCTYPE html>
<html lang="en">
<head>
<meta charset="utf-8">
<title>We Buy Houses Postcard – Harborline Asset Partners</title>
<link rel="stylesheet" href="https://fonts.googleapis.com/css2?family=Oswald:wght@500;700&family=Open+Sans:wght@400;700&display=swap">
<style>
  :root {
    --page: #ffffff;
    --card: #ffffff;
    --red: #b3120f;
    --red-dark: #8e0b09;
    --yellow: #ffd21f;
    --white: #ffffff;
    --ink: #1a1a1a;
    --muted: #444444;
    --navy: #1d3f8f;
    --rule: #c9c9c9;
    --photo-sky: #a9c8e6;
    --photo-grass: #7a9a56;
    --shadow: rgba(0,0,0,0.28);
  }
  * { box-sizing: border-box; margin: 0; padding: 0; }
  html, body { width: 853px; height: 1200px; overflow: hidden; background: var(--page); }
  .canvas { position: relative; width: 853px; height: 1200px; }

  .postcard {
    position: absolute; left: 57px; width: 733px; height: 555px;
    background: var(--card);
    box-shadow: 4px 5px 10px var(--shadow);
    overflow: hidden;
  }
  .postcard--front { top: 28px; }
  .postcard--back { top: 603px; border: 1px solid #e2e2e2; }

  /* Front */
  .offer-panel {
    position: absolute; left: 0; top: 0; width: 300px; height: 100%;
    background: linear-gradient(180deg, var(--red) 0%, var(--red-dark) 100%);
    padding: 26px 20px 0 26px;
    font-family: "Oswald", Arial, sans-serif; text-transform: uppercase;
  }
  .offer-panel__lead { color: var(--yellow); font-weight: 700; font-size: 25px; line-height: 1.2; }
  .offer-panel__cta { color: var(--white); font-weight: 700; font-size: 46px; line-height: 1.1; margin-top: 26px; }
  .offer-panel__phone { color: var(--white); font-weight: 700; font-size: 36px; margin-top: 10px; }
  .offer-panel__terms { color: var(--yellow); font-weight: 700; font-size: 28px; line-height: 1.2; margin-top: 26px; }

  .hero-photo {
    position: absolute; left: 300px; top: 0; right: 0; height: 100%;
    background: linear-gradient(180deg, var(--photo-sky) 0%, #d9e6ef 55%, var(--photo-grass) 100%);
  }
  .offer-band {
    position: absolute; left: 300px; right: 0; bottom: 28px; height: 92px;
    background: var(--red); display: flex; align-items: center; justify-content: center;
    padding: 0 20px; text-align: center;
    font-family: "Oswald", Arial, sans-serif; font-weight: 700; text-transform: uppercase;
    color: var(--yellow); font-size: 27px; line-height: 1.15;
  }

  /* Back */
  .letter {
    position: absolute; left: 36px; top: 42px; width: 330px;
    font-family: "Open Sans", Arial, sans-serif; color: var(--ink); font-size: 16px; line-height: 1.45;
  }
  .letter strong { text-transform: uppercase; font-size: 15px; }
  .letter__list { list-style: disc; margin: 10px 0 14px 22px; }
  .brand {
    margin-top: 28px; text-align: center;
    display: flex; align-items: center; justify-content: center; gap: 10px;
  }
  .brand__mark { width: 18px; height: 18px; background: var(--navy); border-radius: 50%; }
  .brand__name { font-family: "Open Sans", Arial, sans-serif; font-weight: 700; font-size: 19px; color: var(--navy); text-transform: uppercase; }
  .letter__web { margin-top: 22px; text-align: center; font-weight: 700; font-size: 14px; }
  .letter__phone { text-align: center; font-family: "Oswald", Arial, sans-serif; font-weight: 700; font-size: 30px; margin-top: 2px; }
  .letter__return { text-align: center; font-size: 12px; color: var(--muted); margin-top: 8px; line-height: 1.35; }

  .mailing-divider { position: absolute; left: 400px; top: 40px; width: 1px; height: 470px; background: var(--rule); }
</style>
</head>
<body>
<main class="canvas">
  <section class="postcard postcard--front">
    <div class="hero-photo" role="img" aria-label="Photo of a hand passing house keys, a red SOLD sign in front of a home, and a hand holding cash"></div>
    <div class="offer-panel">
      <p class="offer-panel__lead">We buy houses, land and commercial property</p>
      <p class="offer-panel__cta">Fast cash<br>call now</p>
      <p class="offer-panel__phone">555-274-1916</p>
      <p class="offer-panel__terms">Sell as is<br>no costs<br>no commissions</p>
    </div>
    <div class="offer-band">Let us make a fair all cash<br>offer on your house today!</div>
  </section>

  <section class="postcard postcard--back">
    <div class="letter">
      <p>My name is Marcus. <strong>I’m interested in buying your house.</strong> I offer:</p>
      <ul class="letter__list">
        <li>Cash for your house as-is</li>
        <li>No inspections or contingencies</li>
        <li>Fast and flexible closing</li>
        <li>No need to fix or clean out your home</li>
      </ul>
      <p>If you’re interested, please call me. There are no obligations!</p>
      <div class="brand">
        <span class="brand__mark"></span>
        <span class="brand__name">Harborline Asset Partners</span>
      </div>
      <p class="letter__web">www.harborlineassetpartners.com</p>
      <p class="letter__phone">555-274-1916</p>
      <p class="letter__return">587 W Tessaly Ave, Suite 319<br>Baltimore, MD 21209</p>
    </div>
    <div class="mailing-divider"></div>
  </section>
</main>
</body>
</html>
```